Business Card (double-sided) and Stationary Design for dental office

1) Business Card Design: We need a business card design for a dental specialty office.
Texts should contain:
The name of our office "Brindle Oaks Orthodontics"
Tagline: "Specialist in Orthodontic and Maxillofacial Orthopedics"
Tag line: "Creating "Tolvering" smiles for Children and Adults"
Doctor name: "Doctor Name"
Office Address:
"123 Street Name
City, State Zip code"
Office email address: office@brindleoaksortho.com
Website: www.brindleoaksortho.com

We will provide the full office address once the design is selected
Theme: beach, paradise, coastal, wave
We would like to have some creativity in design. Some acceptable ideas: front page: logo and office name. Back page: more detail information, and map to office in form of an island. Please see sample from our other location, but you DON'T HAVE TO USE OR COPY THE SAME CONCEPT.

IF POSSIBLE, PLEASE SUBMIT AT LEAST TWO CONCEPTS: ONE WITH THE BACK LOOKING SIMILAR TO WHAT IS IN THE SAMPLE, AND ONE DIFFERENT.

Color: designer to choose. We have different shade of blues and sand color in our office. Please see logo.

2) Please also design a matching set of stationary that compliment the business card and our logo.

Target Market(s)

Dental

Contact Information for Business Card

See descriptions

Font styles to use
Other font styles liked:
• Matching texts in logo

Colors
0054AA
0677BA
7BADD7
CADEEF
E8F1F8
0094D4
00A9DD
6FCCEA
C7EBF8
E9F6FB
00AB8E
00BBA5
67D7C9
C6EFE9
E9F9F6

Requirements
Must have
• Double-sided
Nice to have
• Beach coastal theme
Should not have
• Any shape or drawing of of tooth or teeth. We don’t need these. You don't necessarily have to just cut and paste the logo art and text as a whole, you have the liberty to rearrange the text.

```html
<!DOCTYPE html>
<html lang="en">
<head>
<meta charset="utf-8">
<title>Brindle Oaks Orthodontics – Cards &amp; Stationery</title>
<link rel="stylesheet" href="https://fonts.googleapis.com/css2?family=Poppins:wght@400;500;600&family=Roboto+Slab:wght@400;700&family=Dancing+Script:wght@500&family=Caveat:wght@500&display=swap">
<style>
:root{
  --teal:#00ab8e;
  --teal-soft:#2fb39c;
  --teal-sheet:#40bba4;
  --teal-pale:#c6efe9;
  --teal-mist:#e9f9f6;
  --blue:#0677ba;
  --ink:#111;
  --paper:#fff;
}
*{box-sizing:border-box;margin:0;padding:0}
html,body{width:761px;height:1200px;overflow:hidden;background:#fff}
body{position:relative;font-family:"Poppins",sans-serif;color:var(--ink)}
.piece{position:absolute;overflow:hidden;background:var(--paper);box-shadow:0 1px 3px rgba(0,0,0,.15)}
.piece svg.bg{position:absolute;inset:0;width:100%;height:100%}
.card{width:342px;height:235px}
.card-front{left:23px;top:55px}
.card-back{left:398px;top:55px}
.envelope-back{left:23px;top:345px}
.envelope-front{left:398px;top:345px}
.letterhead{left:147px;top:653px;width:470px;height:513px}

.brand{position:absolute;display:flex;align-items:center;gap:4px;color:var(--teal)}
.brand-dot{border-radius:50%;background:var(--teal);flex:none}
.brand-name{font-weight:500;white-space:nowrap;line-height:1}
.brand-sub{position:absolute;color:var(--teal);white-space:nowrap;letter-spacing:.5px}

/* card front */
.front-panel{position:absolute;left:0;top:0;width:135px;height:118px;background:linear-gradient(180deg,#cfe6df,#eef6f3);transform:skewY(-3deg);transform-origin:0 0}
.front-title{position:absolute;left:18px;top:62px;transform:rotate(-4deg);transform-origin:0 0;text-align:left}
.front-title .t1{font-family:"Roboto Slab",serif;font-weight:700;font-size:15px;letter-spacing:1px}
.front-title .t2{font-family:"Dancing Script",cursive;font-size:38px;color:var(--teal);line-height:.9;margin-left:-4px}
.front-title .t3{font-family:"Roboto Slab",serif;font-weight:700;font-size:13px;letter-spacing:1px;margin-top:2px}
.note{position:absolute;left:147px;top:45px;width:100px;height:40px;background:#fff;box-shadow:0 2px 4px rgba(0,0,0,.25);transform:rotate(-1deg);font-family:"Caveat",cursive;font-size:9.5px;line-height:1.05;text-align:center;padding-top:5px}
.photo{position:absolute;border-radius:50%;border:3px solid #fff;box-shadow:0 2px 5px rgba(0,0,0,.35)}
.photo-a{left:259px;top:77px;width:76px;height:76px;background:linear-gradient(135deg,#d9a48f,#4b5a6b)}
.photo-b{left:155px;top:112px;width:96px;height:96px;background:linear-gradient(135deg,#7c6a5f,#c9d4dc)}
.photo-c{left:273px;top:150px;width:58px;height:58px;background:linear-gradient(135deg,#caa18a,#f0ede8)}
.web-tag{position:absolute;background:#fff;font-size:4.5px;letter-spacing:.6px;text-align:center;line-height:9px;height:9px;width:80px}

/* card back */
.spec{position:absolute;left:68px;top:62px;font-size:7.3px;font-weight:600;white-space:nowrap}
.slogan{position:absolute;left:130px;top:78px;font-family:"Dancing Script",cursive;font-size:14px;color:var(--teal)}
.cta{position:absolute;left:160px;top:104px;width:85px;text-align:center;font-family:"Roboto Slab",serif;font-size:7px;line-height:1.3}
.details{position:absolute;left:138px;top:155px;font-size:6.2px;display:grid;grid-template-columns:65px 12px auto;row-gap:1px}
.details .lbl{font-family:"Roboto Slab",serif;font-weight:700;color:var(--teal)}
.details .sep{color:var(--teal)}

/* envelope back */
.env-address{position:absolute;left:70px;top:168px;font-family:"Roboto Slab",serif;font-size:5.4px;line-height:1.45}
.env-address .name{font-family:"Poppins",sans-serif;font-weight:600;font-size:6.3px;margin-bottom:4px}
.env-address .doc{font-family:"Poppins",sans-serif;font-weight:600;font-size:5.8px;margin-bottom:3px}

/* letterhead */
.lh-frame{position:absolute;left:7px;top:7px;right:7px;bottom:7px;border:1px solid #777}
.lh-rule{position:absolute;left:7px;right:7px;top:131px;border-top:1px solid #ddd}
.lh-contact{position:absolute;right:28px;top:33px;text-align:right;font-family:"Roboto Slab",serif;font-size:7px;line-height:1.6}
.lh-contact .doc{font-family:"Poppins",sans-serif;font-weight:600;font-size:6.5px;margin-bottom:2px}
.fairy{position:absolute;border-radius:50%;opacity:.35}
</style>
</head>
<body>

<!-- Business card front -->
<section class="piece card card-front">
  <svg class="bg" viewBox="0 0 342 235" preserveAspectRatio="none">
    <path d="M0 205 C120 202 210 185 260 150 C315 110 318 50 302 0 L342 0 L342 235 L0 235 Z" fill="var(--teal)"/>
  </svg>
  <div class="front-panel"></div>
  <div class="brand" style="left:28px;top:28px">
    <span class="brand-dot" style="width:12px;height:12px"></span>
    <span class="brand-name" style="font-size:8.5px">Brindle Oaks</span>
  </div>
  <div class="brand-sub" style="left:30px;top:44px;font-size:3.6px">Pediatric Dentistry &amp; Orthodontics</div>
  <div class="front-title">
    <div class="t1">BRINDLE OAKS</div>
    <div class="t2">SMILES</div>
    <div class="t3">ORTHODONTICS</div>
  </div>
  <div class="note">"Creating "Tolvering"<br>smiles for Children &amp;<br>Adults"</div>
  <div class="photo photo-a" role="img" aria-label="Photo of a smiling patient at a dental check-up"></div>
  <div class="photo photo-b" role="img" aria-label="Photo of a dentist treating an older patient"></div>
  <div class="photo photo-c" role="img" aria-label="Photo of a smiling young woman"></div>
  <div class="web-tag" style="left:34px;top:216px">www.brindleoaksortho.com</div>
</section>

<!-- Business card back -->
<section class="piece card card-back">
  <svg class="bg" viewBox="0 0 342 235" preserveAspectRatio="none">
    <rect width="342" height="235" fill="var(--teal-soft)"/>
    <path d="M36 0 C22 110 110 200 342 205 L342 175 C336 110 332 40 316 0 Z" fill="#fff"/>
    <path d="M316 0 C332 40 336 110 342 175 L342 170 C334 100 330 40 322 0 Z" fill="#7fd0c1"/>
  </svg>
  <div class="brand" style="left:50px;top:18px">
    <span class="brand-dot" style="width:14px;height:14px"></span>
    <span class="brand-name" style="font-size:8.5px">Brindle Oaks</span>
  </div>
  <div class="brand-sub" style="left:50px;top:36px;font-size:3.6px">Pediatric Dentistry &amp; Orthodontics</div>
  <div class="spec">SPECIALIST IN ORTHODONTIC AND MAXILLOFACIAL ORTHOPEDICS</div>
  <div class="slogan">Let's Take Care of our Teeth</div>
  <div class="cta">GET A FREE<br>CONSULTATION</div>
  <svg style="position:absolute;left:194px;top:128px" width="18" height="22" viewBox="0 0 18 22">
    <path d="M3 2 L10 2 L10 14 L14 14 L8 20 L2 14 L6 14 L6 6 L3 6 Z" fill="none" stroke="#333" stroke-width=".8"/>
  </svg>
  <div class="details">
    <span class="lbl">DOCTOR NAME</span><span class="sep">:</span><span>"Doctor Name"</span>
    <span class="lbl">OFFICE ADDRESS</span><span class="sep">:</span><span>"123 Street Name City,<br>&nbsp;State Zip code"</span>
  </div>
  <div class="fairy" role="img" aria-label="Faint illustration of a tooth fairy" style="left:290px;top:110px;width:45px;height:70px;background:#f5e6d8"></div>
  <div class="web-tag" style="left:23px;top:215px">www.brindleoaksortho.com</div>
  <div class="web-tag" style="left:113px;top:215px">office@brindleoaksortho.com</div>
</section>

<!-- Envelope back -->
<section class="piece card envelope-back">
  <svg class="bg" viewBox="0 0 342 235" preserveAspectRatio="none">
    <rect width="342" height="235" fill="var(--teal)"/>
    <path d="M3 3 L339 3 L339 128 C330 170 330 215 302 232 L3 232 Z" fill="#fff"/>
    <path d="M3 3 L339 3 L171 112 Z" fill="var(--teal)"/>
  </svg>
  <span class="brand-dot" style="position:absolute;left:17px;top:165px;width:44px;height:44px"></span>
  <div class="env-address">
    <div class="name">BRINDLE OAKS ORTHODONTICS</div>
    <div class="doc">DOCTOR NAME</div>
    <div>123 Street Name City, State Zip code</div>
    <div style="margin-top:2px">office@brindleoaksortho.com</div>
    <div>www.brindleoaksortho.com</div>
  </div>
</section>

<!-- Envelope front -->
<section class="piece card envelope-front">
  <svg class="bg" viewBox="0 0 342 235" preserveAspectRatio="none">
    <rect width="342" height="235" fill="var(--teal)"/>
    <path d="M30 3 C18 100 70 200 250 206 L338 206 L338 3 Z" fill="#9fd8cd"/>
    <path d="M34 3 C24 100 75 196 250 200 L336 200 C338 150 335 60 316 3 Z" fill="#fff"/>
  </svg>
  <div class="brand" style="left:233px;top:62px">
    <span class="brand-dot" style="width:14px;height:14px"></span>
    <span class="brand-name" style="font-size:9px">Brindle Oaks</span>
  </div>
  <div class="brand-sub" style="left:233px;top:80px;font-size:3.8px">Pediatric Dentistry &amp; Orthodontics</div>
</section>

<!-- Letterhead -->
<section class="piece letterhead">
  <svg class="bg" viewBox="0 0 470 513" preserveAspectRatio="none">
    <path d="M0 292 C30 420 160 470 470 465 L470 513 L0 513 Z" fill="var(--teal-sheet)"/>
    <path d="M0 292 C30 420 160 470 470 465 L470 472 C160 478 25 425 0 300 Z" fill="#a6ddd2"/>
  </svg>
  <div class="lh-frame"></div>
  <div class="lh-rule"></div>
  <div class="brand" style="left:28px;top:40px">
    <span class="brand-dot" style="width:30px;height:30px"></span>
    <span class="brand-name" style="font-size:15px">Brindle Oaks</span>
  </div>
  <div class="brand-sub" style="left:28px;top:76px;font-size:5.8px">Pediatric Dentistry &amp; Orthodontics</div>
  <div class="lh-contact">
    <div class="doc">DOCTOR NAME</div>
    <div>123 Street Name</div>
    <div>City, State Zip code</div>
    <div>office@brindleoaksortho.com</div>
    <div>www.brindleoaksortho.com</div>
  </div>
  <div class="fairy" role="img" aria-label="Faint illustration of a tooth fairy" style="left:10px;top:135px;width:110px;height:110px;background:#f3ecf3"></div>
  <div class="fairy" role="img" aria-label="Faint illustration of a tooth fairy" style="left:370px;top:215px;width:80px;height:130px;background:#f6eee8"></div>
</section>

</body>
</html>
```